KLV Plant Services

We are a heavy diesel mechanical business with additional air con certificates, remapping engine rebuilt

Contact Information for Business Card

Company Name, Director Name, Managing Director, Contact details, email and website

Font styles to use
Serif
Script

```html
<!DOCTYPE html>
<html lang="en">
<head>
<meta charset="utf-8">
<title>KLV Plant Services – Business Card</title>
<link rel="stylesheet" href="https://fonts.googleapis.com/css2?family=Libre+Baskerville:wght@400;700&family=Dancing+Script:wght@600&display=swap">
<style>
  :root {
    --navy: #02025e;
    --paper: #f3f4f6;
    --backdrop: #d9d9d9;
    --ink: #000000;
    --white: #ffffff;
    --mark-soft: #4a50c8;
  }
  * { margin: 0; padding: 0; box-sizing: border-box; }
  html, body { width: 1200px; height: 1040px; overflow: hidden; }
  body {
    background: var(--backdrop);
    font-family: "Libre Baskerville", Georgia, serif;
    position: relative;
  }
  .card {
    position: absolute;
    left: 282px;
    width: 644px;
    height: 366px;
    border-radius: 18px;
    overflow: hidden;
  }
  .card--front { top: 130px; background: var(--paper); }
  .card--back { top: 567px; background: var(--navy); }

  .card__wave { position: absolute; inset: 0; width: 100%; height: 100%; }

  .brand {
    position: absolute;
    color: var(--navy);
    font-weight: 700;
    line-height: 1;
  }
  .brand__short { display: block; font-size: 50px; letter-spacing: 1px; }
  .brand__long { display: block; font-size: 16px; margin-top: 6px; }
  .card--front .brand { left: 104px; top: 110px; }

  .person {
    position: absolute;
    right: 40px;
    top: 120px;
    text-align: right;
    color: var(--white);
  }
  .person__name { font-size: 22px; font-weight: 700; line-height: 1.2; }
  .person__role {
    font-family: "Dancing Script", "Brush Script MT", cursive;
    font-weight: 600;
    font-size: 20px;
    line-height: 1.1;
    margin-top: 2px;
  }

  .address {
    position: absolute;
    right: 40px;
    top: 212px;
    text-align: right;
    color: var(--white);
    font-size: 14px;
    line-height: 20px;
    font-style: normal;
  }
  .contacts {
    position: absolute;
    right: 38px;
    top: 268px;
    list-style: none;
    color: var(--white);
    font-size: 14px;
    line-height: 20.5px;
  }
  .contacts li { display: flex; justify-content: flex-end; align-items: center; gap: 9px; }
  .contacts svg { width: 13px; height: 13px; fill: var(--white); flex: none; }

  .card--back .brand {
    left: 0; right: 0; top: 132px;
    text-align: center;
    color: var(--mark-soft);
  }
  .card--back .brand__short { font-size: 62px; }
  .card--back .brand__long { font-size: 21px; margin-top: 8px; }

  .back-web {
    position: absolute;
    left: 0; right: 0; top: 322px;
    text-align: center;
    color: var(--white);
    font-size: 14px;
    letter-spacing: 3.5px;
  }
</style>
</head>
<body>
  <section class="card card--front" aria-label="Business card front">
    <svg class="card__wave" viewBox="0 0 644 366" preserveAspectRatio="none" aria-hidden="true">
      <path d="M0,226 C90,296 200,318 300,226 S490,44 644,62 L644,366 L0,366 Z" fill="var(--ink)"/>
      <path d="M0,250 C90,316 206,326 304,232 S494,58 644,70 L644,366 L0,366 Z" fill="var(--white)"/>
      <path d="M0,254 C90,318 208,328 306,234 S496,62 644,72 L644,366 L0,366 Z" fill="var(--navy)"/>
    </svg>

    <div class="brand">
      <span class="brand__short">KLV</span>
      <span class="brand__long">Plant Services</span>
    </div>

    <div class="person">
      <p class="person__name">Daniel Harper</p>
      <p class="person__role">Managing Director</p>
    </div>

    <address class="address">
      2710 Harbor Ridge Road<br>
      Glen Oaks, NY 11004
    </address>

    <ul class="contacts">
      <li>(555) 0142-7781
        <svg viewBox="0 0 24 24" aria-hidden="true"><path d="M6.6 10.8a15.1 15.1 0 0 0 6.6 6.6l2.2-2.2c.3-.3.7-.4 1-.2 1.1.4 2.3.6 3.6.6.6 0 1 .4 1 1V20c0 .6-.4 1-1 1A17 17 0 0 1 3 4c0-.6.4-1 1-1h3.5c.6 0 1 .4 1 1 0 1.3.2 2.5.6 3.6.1.3 0 .7-.2 1z"/></svg>
      </li>
      <li>name@KLV.com
        <svg viewBox="0 0 24 24" aria-hidden="true"><rect x="2" y="5" width="20" height="14"/><path d="M2 5l10 8 10-8" fill="none" stroke="var(--navy)" stroke-width="1.8"/></svg>
      </li>
      <li>www.KLV.com
        <svg viewBox="0 0 24 24" aria-hidden="true"><circle cx="12" cy="12" r="10"/><path d="M8 7c2 1 3 3 2 5s-3 2-2 5M15 5c-1 2 1 3 3 4M14 14c2 0 3 2 2 4" stroke="var(--navy)" stroke-width="2" fill="none"/></svg>
      </li>
    </ul>
  </section>

  <section class="card card--back" aria-label="Business card back">
    <div class="brand">
      <span class="brand__short">KLV</span>
      <span class="brand__long">Plant Services</span>
    </div>
    <p class="back-web">www.KLV.com</p>
  </section>
</body>
</html>
```